Bright Harbor Counseling Letterhead for hip modern business

I would like some ombre use of the colors in the logo hip letterhead that incorporates logo colors and feel, needs to connect with young professionals and college students. i need to be able to write letters to schools to excuse absences as well. i like color blocks on one side preferably using colors from the attached logo design.

Target Market(s)

high income young people, young adults and college students

Industry/Entity Type

mental health

Font styles to use
Serif
Sans Serif

Colors
0054AA
0677BA
7BADD7
CADEEF
E8F1F8
0094D4
00A9DD
6FCCEA
C7EBF8
E9F6FB
00AB8E
00BBA5
67D7C9
C6EFE9
E9F9F6
59FF00
82FF00
B8FF75
E3FFCB
F4FFEA
A7469A
B969AE
D3A5CF
EDDBEB
F8F0F9
6B429C
8869AF
B7A5CE
E3DAEB
F3F0F8

Requirements
Must have
• a modern hip feel, somewhat color

```html
<!DOCTYPE html>
<html lang="en">
<head>
<meta charset="utf-8">
<title>Bright Harbor Counseling Letterhead</title>
<link href="https://fonts.googleapis.com/css2?family=Questrial&family=Poppins:wght@400;500;600&display=swap" rel="stylesheet">
<style>
  :root {
    --paper-light: #f3f3f3;
    --paper-dark: #dedede;
    --ink: #2b2b2b;
    --body-ink: #3a3a3a;
    --brand-blue: #3a73c0;
    --plum-deep: #8f2f7a;
    --plum-mid: #b9689d;
    --lavender: #8869af;
    --signature-tone: #cfcfd4;
  }
  * { margin: 0; padding: 0; box-sizing: border-box; }
  html, body { width: 960px; height: 1200px; overflow: hidden; }
  body { background: #ffffff; font-family: "Questrial", sans-serif; color: var(--ink); }

  .letterhead {
    position: relative;
    width: 960px;
    height: 1200px;
    background: linear-gradient(100deg, var(--paper-light) 0%, #e9e9e9 55%, var(--paper-dark) 100%);
    overflow: hidden;
  }

  .brand-name {
    position: absolute;
    left: 88px;
    top: 118px;
    font-family: "Questrial", sans-serif;
    font-size: 34px;
    line-height: 1;
    color: var(--ink);
    display: flex;
    align-items: center;
    gap: 12px;
  }
  .brand-dot {
    width: 16px; height: 16px; border-radius: 50%;
    background: var(--plum-mid);
  }

  .contact-address {
    position: absolute;
    right: calc(960px - 658px);
    top: 116px;
    text-align: right;
    font-family: "Poppins", sans-serif;
    font-size: 14px;
    line-height: 18px;
    color: var(--ink);
  }
  .contact-web { color: var(--brand-blue); font-weight: 600; letter-spacing: 0.4px; margin-top: 1px; }

  .contact-divider {
    position: absolute;
    left: 671px; top: 119px;
    width: 1px; height: 56px;
    background: var(--ink);
  }

  .contact-lines {
    position: absolute;
    left: 688px; top: 117px;
    font-family: "Poppins", sans-serif;
    font-size: 14px;
    line-height: 18px;
    list-style: none;
    color: var(--ink);
  }
  .contact-lines li { display: flex; align-items: center; gap: 6px; }
  .contact-lines svg { width: 11px; height: 11px; fill: var(--brand-blue); }

  .letter {
    position: absolute;
    left: 87px; top: 350px;
    width: 792px;
  }
  .salutation { font-size: 22px; color: var(--ink); margin-bottom: 40px; }
  .letter p.body-copy {
    font-size: 13.2px;
    line-height: 18.3px;
    color: var(--body-ink);
    text-align: justify;
    margin-bottom: 18.3px;
  }
  .closing { position: absolute; left: 87px; top: 798px; font-size: 13.2px; color: var(--body-ink); }
  .signature {
    position: absolute; left: 87px; top: 843px;
    width: 124px; height: 68px;
    background: linear-gradient(90deg, var(--signature-tone), #e2e2e6);
    border-radius: 4px;
  }

  .footer-wave { position: absolute; left: 0; bottom: 0; width: 960px; height: 80px; }
</style>
</head>
<body>
<main class="letterhead">
  <header>
    <div class="brand-name"><span>Bright Harbor Counseling</span><span class="brand-dot"></span></div>

    <address class="contact-address" style="font-style:normal">
      <div>2140 Willow Crest Drive</div>
      <div>Portland, Oregon 97214</div>
      <div class="contact-web">www.brightharbor.com</div>
    </address>
    <div class="contact-divider"></div>
    <ul class="contact-lines">
      <li><svg viewBox="0 0 12 12"><path d="M2.5 0.8l2 2.3-1.1 1.3c0.7 1.6 2 2.9 3.6 3.6l1.3-1.1 2.3 2-1.2 2.1C5 10.6 1.4 7 0.5 2z"/></svg>503-555-0142</li>
      <li><svg viewBox="0 0 12 12"><rect x="3" y="0.5" width="6" height="3"/><rect x="0.5" y="4" width="11" height="5" rx="1"/><rect x="3" y="8" width="6" height="3.5"/></svg>503-555-0187</li>
      <li><svg viewBox="0 0 12 12"><path d="M0.5 2h11v8h-11z M1.2 2.6L6 6.5l4.8-3.9" stroke="#fff" stroke-width="0.8"/></svg>hello@brightharbor.com</li>
    </ul>
  </header>

  <section class="letter">
    <p class="salutation">Dear Mr. Carter,</p>
    <p class="body-copy">Lorem ipsum dolor sit amet, consectetur adipiscing elit. Donec orci purus, luctus vitae dignissim eu, iaculis sed purus. Vivamus faucibus, ipsum nec aliquet viverra, leo mauris condimentum ligula, sit amet sagittis enim ligula quis arcu. Nam egestas tortor id nisi porttitor mattis. In tortor ante, ultricies in suscipit a, tempus non massa. Vivamus et auctor mi. Fusce vel massa nulla. Phasellus nec eros mauris, et scelerisque orci.</p>
    <p class="body-copy">Donec malesuada orci vitae nulla accumsan porta a id massa. Quisque accumsan iaculis magna sit amet fringilla. Maecenas consequat, magna eget tincidunt semper, odio nibh rutrum mi, id feugiat ante nisi eu risus. Vestibulum nunc orci, rhoncus a placerat in, ultricies in mi. Cras mattis varius eros, vel fringilla nisi suscipit eget. Quisque scelerisque sagittis nulla at porttitor.</p>
    <p class="body-copy">Sed id augue vitae urna euismod commodo aliquet a quam. Pellentesque arcu velit, cursus et malesuada ut, consequat et diam. Nullam erat sem, rhoncus id ullamcorper vitae, rhoncus et arcu. In ultricies ultricies nulla, ut rutrum nisi iaculis at. Donec eu magna a metus ornare faucibus. Fusce aliquet faucibus ultricies. Morbi semper, est id tincidunt gravida, sem arcu adipiscing lacus, ac bibendum nulla leo eu purus. Quisque nec diam sed risus consectetur a ccumsan quis quis nibh. Vestibulum id purus lorem.</p>
    <p class="body-copy">It is a long established fact that a reader will be distracted by the readable content of a page when looking at its layout. The point of using Lorem Ipsum is that it has a more-or-less normal distribution of letters, as opposed to using 'Content here, content here', making it look like readable English. Many desktop publishing packages</p>
  </section>

  <p class="closing">Sincerely,</p>
  <div class="signature" role="img" aria-label="Handwritten signature of the counselor"></div>

  <svg class="footer-wave" viewBox="0 0 960 80" preserveAspectRatio="none" aria-hidden="true">
    <defs>
      <linearGradient id="plumBand" x1="0" x2="1" y1="0" y2="0">
        <stop offset="0" stop-color="#93327c"/>
        <stop offset="0.5" stop-color="#b9689d"/>
        <stop offset="1" stop-color="#8f2f7a"/>
      </linearGradient>
    </defs>
    <path d="M420 76 C 600 62, 760 34, 860 36 C 910 37, 940 50, 960 64 L960 66 C 930 52, 900 44, 860 43 C 760 42, 620 66, 420 80 Z" fill="var(--lavender)"/>
    <path d="M0 48 C 200 80, 420 86, 640 70 C 760 60, 840 44, 880 44 C 920 45, 945 55, 960 68 L960 80 L0 80 Z" fill="url(#plumBand)"/>
  </svg>
</main>
</body>
</html>
```